Pressure Washing Hog Confinements

We clean and disinfect Hog confinements in-order to receive new pigs.

Needs to emphasis Clean Healthy barns (pigs), work done in timely manner, 100% satisfied, Bio-security rules followed. I do not have specific colors, no logo's.

Contact Information will be sent once design is agreed on.
Business Name - Brandt & Daughters Power Washing
Phone Number - Send latter
E-mail - Send latter
Web Address - Send latter

Target Market(s)

Farmers

Industry/Entity Type

Business

Requirements
Must have
• We are Insured
Bio-Security
100% Satisfied
Water Conservation

Size - 2 sided Postcard 8.5" x 5.5"
Nice to have
• I want to emphasize healthy and happy pigs because of a quality job done. Picture of pigs dose not need to be used but may be just an example.

Also attached is picture of a barn I would like to see used. on the back side. Every owner seeing this will know this is a hog barn and have an idea what we do.

```html
<!DOCTYPE html>
<html lang="en">
<head>
<meta charset="utf-8">
<title>Brandt &amp; Daughters Power Washing – Postcard</title>
<link rel="stylesheet" href="https://fonts.googleapis.com/css2?family=Alegreya:wght@400&family=Arimo:wght@400;700&display=swap">
<style>
  :root {
    --canvas: #f2f2f0;
    --maroon: #8b4049;
    --gold: #f2b53a;
    --ink: #4a4f55;
    --ink-dark: #3a3a3a;
    --panel: #e4e4e6;
    --paper: #ffffff;
    --sky-top: #3f86d3;
    --sky-low: #b4d3ec;
    --ground: #d3cab8;
  }
  * { box-sizing: border-box; margin: 0; padding: 0; }
  html, body { width: 1200px; height: 572px; overflow: hidden; background: var(--canvas); }
  .canvas { position: relative; width: 1200px; height: 572px; }
  .card {
    position: absolute; top: 101px; width: 570px; height: 369px;
    overflow: hidden; background: var(--paper);
    box-shadow: 0 2px 6px rgba(0,0,0,.25);
  }
  .card--front { left: 20px; }
  .card--back { left: 610px; }
  .wave { position: absolute; left: 0; top: 0; width: 570px; height: 369px; }

  /* front */
  .barn-photo {
    position: absolute; inset: 0;
    background: linear-gradient(180deg, var(--sky-top) 0%, var(--sky-low) 52%, #9aa9b5 62%, var(--ground) 76%, #c9bfab 100%);
  }
  .headline {
    position: absolute; left: 27px; top: 20px; width: 530px;
    font-family: "Alegreya", Georgia, serif; font-weight: 400; font-size: 25px; line-height: 29px;
    color: var(--ink); text-transform: uppercase; letter-spacing: .3px;
  }
  .subline {
    position: absolute; left: 27px; top: 96px; width: 520px;
    font-family: "Alegreya", Georgia, serif; font-weight: 400; font-size: 16.5px; line-height: 19px;
    color: var(--ink-dark);
  }
  .front-name {
    position: absolute; right: 15px; top: 322px;
    font-family: "Alegreya", Georgia, serif; font-weight: 400; font-size: 30px; line-height: 36px;
    color: var(--gold); white-space: nowrap;
  }

  /* back */
  .side-panel { position: absolute; left: 0; top: 0; width: 277px; height: 369px; background: var(--panel); }
  .pig-photo {
    position: absolute; left: 0; top: 0; width: 277px; height: 185px;
    background: linear-gradient(135deg, #d6d6d8 0%, #ebebed 50%, #dcdcde 100%);
  }
  .benefits { position: absolute; left: 16px; top: 33px; font-family: "Arimo", Arial, sans-serif; }
  .benefits__title { font-size: 18.5px; font-weight: 400; color: var(--maroon); line-height: 24px; margin-bottom: 1px; }
  .benefits__list { list-style: none; }
  .benefits__item { display: flex; align-items: center; gap: 5px; font-size: 18.5px; line-height: 25px; color: var(--ink-dark); }
  .benefits__tick { width: 16px; height: 16px; flex: none; }
  .contact { position: absolute; left: 17px; top: 236px; font-family: "Arimo", Arial, sans-serif; color: var(--ink-dark); }
  .contact__name { font-family: "Alegreya", Georgia, serif; font-weight: 400; font-size: 20px; line-height: 26px; color: var(--ink); margin-bottom: 3px; }
  .contact__line { font-size: 13.5px; line-height: 19.5px; }
  .contact__label { display: inline-block; width: 20px; }

  .return-address { position: absolute; left: 298px; top: 23px; font-family: "Arimo", Arial, sans-serif; font-size: 8.5px; line-height: 12.5px; color: #222; font-style: normal; }
  .return-address strong { font-size: 9px; }
  .postage {
    position: absolute; left: 486px; top: 30px; width: 51px; height: 51px;
    border: 1px solid #444; font-family: "Arimo", Arial, sans-serif; font-size: 5.5px; line-height: 7px;
    text-align: center; padding-top: 4px; color: #222;
  }
  .postage b { font-size: 7.5px; display: block; line-height: 9px; }
  .recipient-box {
    position: absolute; left: 436px; top: 95px; width: 101px; height: 51px;
    border: 1px solid #444; font-family: "Arimo", Arial, sans-serif; font-size: 8.5px; line-height: 11px;
    padding: 12px 0 0 11px; color: #222;
  }
  .address-line { position: absolute; left: 308px; width: 218px; height: 1px; background: #333; }
  .address-line--1 { top: 180px; }
  .address-line--2 { top: 200px; }
  .address-line--3 { top: 220px; }
  .address-line--4 { top: 241px; }
  .website {
    position: absolute; right: 28px; top: 336px;
    font-family: "Arimo", Arial, sans-serif; font-size: 19.5px; line-height: 22px; color: var(--paper);
  }
</style>
</head>
<body>
<main class="canvas">

  <section class="card card--front" aria-label="Postcard front">
    <div class="barn-photo" role="img" aria-label="Photo of a long hog confinement barn with four blue feed bins under a clear blue sky"></div>
    <h1 class="headline">Healthy and happy pigs because<br>of a quality job done</h1>
    <p class="subline">We clean and disinfect Hog confinements<br>in-order to receive new pigs</p>
    <svg class="wave" viewBox="0 0 570 369" aria-hidden="true">
      <defs>
        <linearGradient id="silver-front" x1="0" x2="1" y1="0" y2="0">
          <stop offset="0" stop-color="#ffffff"/>
          <stop offset=".45" stop-color="#b9c0c4"/>
          <stop offset=".8" stop-color="#5d7b80"/>
          <stop offset="1" stop-color="#9fb2b4"/>
        </linearGradient>
      </defs>
      <path d="M0,300 C110,342 260,290 570,252 L570,262 C260,300 110,352 0,312 Z" fill="url(#silver-front)"/>
      <path d="M0,312 C110,352 260,300 570,262 L570,369 L0,369 Z" fill="var(--maroon)"/>
    </svg>
    <p class="front-name">Brandt and Daughters</p>
  </section>

  <section class="card card--back" aria-label="Postcard back">
    <div class="side-panel"></div>
    <div class="pig-photo" role="img" aria-label="Faded photo of clean healthy pigs"></div>

    <div class="benefits">
      <h2 class="benefits__title">WE ARE INSURED</h2>
      <ul class="benefits__list">
        <li class="benefits__item"><svg class="benefits__tick" viewBox="0 0 16 16" aria-hidden="true"><rect x="1.5" y="3.5" width="11" height="11" fill="none" stroke="var(--maroon)" stroke-width="1.6"/><path d="M4 8.5 L7 11.5 L14.5 2" fill="none" stroke="var(--maroon)" stroke-width="2.2"/></svg>Clean Healthy barns</li>
        <li class="benefits__item"><svg class="benefits__tick" viewBox="0 0 16 16" aria-hidden="true"><rect x="1.5" y="3.5" width="11" height="11" fill="none" stroke="var(--maroon)" stroke-width="1.6"/><path d="M4 8.5 L7 11.5 L14.5 2" fill="none" stroke="var(--maroon)" stroke-width="2.2"/></svg>Work done in timely manner</li>
        <li class="benefits__item"><svg class="benefits__tick" viewBox="0 0 16 16" aria-hidden="true"><rect x="1.5" y="3.5" width="11" height="11" fill="none" stroke="var(--maroon)" stroke-width="1.6"/><path d="M4 8.5 L7 11.5 L14.5 2" fill="none" stroke="var(--maroon)" stroke-width="2.2"/></svg>100% satisfied</li>
        <li class="benefits__item"><svg class="benefits__tick" viewBox="0 0 16 16" aria-hidden="true"><rect x="1.5" y="3.5" width="11" height="11" fill="none" stroke="var(--maroon)" stroke-width="1.6"/><path d="M4 8.5 L7 11.5 L14.5 2" fill="none" stroke="var(--maroon)" stroke-width="2.2"/></svg>Bio-security</li>
        <li class="benefits__item"><svg class="benefits__tick" viewBox="0 0 16 16" aria-hidden="true"><rect x="1.5" y="3.5" width="11" height="11" fill="none" stroke="var(--maroon)" stroke-width="1.6"/><path d="M4 8.5 L7 11.5 L14.5 2" fill="none" stroke="var(--maroon)" stroke-width="2.2"/></svg>Water conservation</li>
      </ul>
    </div>

    <div class="contact">
      <p class="contact__name">Brandt &amp; Daughters</p>
      <p class="contact__line"><span class="contact__label">P :</span>555-014-2290</p>
      <p class="contact__line"><span class="contact__label">E :</span>info@brandtdaughters.com</p>
    </div>

    <address class="return-address">
      <strong>Return Address</strong><br>
      Brandt &amp; Daughters<br>
      Street Name, City Name<br>
      State Zip Code
    </address>

    <div class="postage">PRSRT STD<br>ECRWSS<br>U.S POSTAGE<b>PAID</b>EDDM Retail</div>
    <div class="recipient-box">Local<br>Postal Customer</div>

    <div class="address-line address-line--1"></div>
    <div class="address-line address-line--2"></div>
    <div class="address-line address-line--3"></div>
    <div class="address-line address-line--4"></div>

    <svg class="wave" viewBox="0 0 570 369" aria-hidden="true">
      <defs>
        <linearGradient id="silver-back" x1="0" x2="1" y1="0" y2="0">
          <stop offset="0" stop-color="#ffffff"/>
          <stop offset=".45" stop-color="#b9c0c4"/>
          <stop offset=".8" stop-color="#5d7b80"/>
          <stop offset="1" stop-color="#9fb2b4"/>
        </linearGradient>
      </defs>
      <path d="M0,312 C120,342 280,290 570,266 L570,276 C280,300 120,352 0,322 Z" fill="url(#silver-back)"/>
      <path d="M0,322 C120,352 280,300 570,276 L570,369 L0,369 Z" fill="var(--maroon)"/>
    </svg>
    <p class="website">www.brandtdaughters.com</p>
  </section>

</main>
</body>
</html>
```